New Business card design to reflect rebrand

I would like a business card design with a good base colour for our new logo and also a placeholder for a profile pic of the card holder. the design needs to be editable to the point that we can easily change the picture of the person and use that design for printmerlo etc. we are looking at a metalic finish business card so will need a good base colour to bring out the finish.

Target Market(s)

prospective customers

Industry/Entity Type

Business

Contact Information for Business Card

I would like one editable design that we can change the name of the card holder and profile picture. The design need to be in a format that be send to printmerlo etc.

Our address is Fenwick Lodge, Copse Lane, Ashford Vale, GU14 3TP Tel no. 01483 556172

Requirements
Must have
• place holder for a profile pic for the card holder. in AI or preferably PSD format

```html
<!DOCTYPE html>
<html lang="en">
<head>
<meta charset="utf-8">
<title>Corvane Facility Group – Business Card</title>
<link href="https://fonts.googleapis.com/css2?family=Source+Sans+3:wght@400;600;700&display=swap" rel="stylesheet">
<style>
  :root {
    --backdrop: #dcd9d5;
    --card: #f4f3f1;
    --slate: #3e5068;
    --orange: #ee6a12;
    --ink: #2b2f36;
    --icon: #46566e;
  }
  * { margin: 0; padding: 0; box-sizing: border-box; }
  html, body {
    width: 1200px; height: 900px; overflow: hidden;
    background: var(--backdrop);
    font-family: "Source Sans 3", sans-serif;
  }
  .card {
    position: absolute; left: 120px; top: 155px;
    width: 960px; height: 590px;
    background: var(--card);
    border-radius: 26px;
    box-shadow: 0 18px 40px rgba(0,0,0,0.12);
  }
  .profile-photo {
    position: absolute; left: 74px; top: 78px;
    width: 254px; height: 352px;
    border-radius: 10px;
    background: linear-gradient(180deg, var(--orange) 0%, var(--orange) 38%, #2a2f3a 62%, #1d2129 100%);
  }
  .holder-name {
    position: absolute; left: 34px; top: 458px; width: 334px;
    text-align: center;
    font-size: 44px; font-weight: 600; letter-spacing: 0.5px;
    color: var(--slate);
  }
  .holder-name .surname { color: var(--orange); }
  .brand {
    position: absolute; left: 458px; top: 78px; width: 430px;
    display: flex; align-items: center; justify-content: center; gap: 18px;
  }
  .brand-mark {
    width: 34px; height: 34px; background: var(--orange); flex: none;
  }
  .brand-name {
    font-size: 44px; font-weight: 700; line-height: 1.08;
    color: var(--slate); text-transform: uppercase; letter-spacing: 1.5px;
  }
  .contact {
    position: absolute; left: 470px; top: 318px;
    list-style: none; font-size: 25px; color: var(--ink);
  }
  .contact li { display: flex; align-items: center; gap: 14px; height: 42px; }
  .contact svg { width: 18px; height: 18px; fill: var(--icon); }
  .address {
    position: absolute; left: 462px; top: 448px;
    font-size: 25px; line-height: 36px; color: var(--ink); font-style: normal;
  }
</style>
</head>
<body>
  <section class="card">
    <div class="profile-photo" role="img" aria-label="Profile photo of the card holder"></div>
    <h1 class="holder-name">DANIEL <span class="surname">REEVE</span></h1>

    <div class="brand">
      <span class="brand-mark"></span>
      <span class="brand-name">Corvane<br>Facility Group</span>
    </div>

    <ul class="contact">
      <li>
        <svg viewBox="0 0 24 24" aria-hidden="true"><path d="M6.6 10.8a15.1 15.1 0 0 0 6.6 6.6l2.2-2.2c.3-.3.7-.4 1-.2 1.1.4 2.3.6 3.6.6.6 0 1 .4 1 1V20c0 .6-.4 1-1 1A17 17 0 0 1 3 4c0-.6.4-1 1-1h3.5c.6 0 1 .4 1 1 0 1.3.2 2.5.6 3.6.1.3 0 .7-.2 1z"/></svg>
        <span>01483 556172</span>
      </li>
      <li>
        <svg viewBox="0 0 24 24" aria-hidden="true"><path d="M2 5h20v14H2z"/><path d="M3 6.5l9 7 9-7" fill="none" stroke="var(--card)" stroke-width="1.6"/></svg>
        <span>info@corvanegroup.com</span>
      </li>
    </ul>

    <address class="address">
      Fenwick Lodge, Copse Lane,<br>
      Ashford Vale, GU14 3TP
    </address>
  </section>
</body>
</html>
```